Toriva Letterhead

Hi Kelvara:

I would like a card that is cleanly laid out, with adequate white space for the text to breathe. We don't need a fax number.
The address is:
4120 Marlow Crest Drive, Suite 210
Plano Texas 75081

Gordon R. Whitfield
Managing Director
469.517.3846 (d)
214.639.4705 (m)
gwhitfield@torivafunds.example

The Kanji characters for Toriva are: 朝凪
It would be good if you could fit the kanji in as well.

Thank you, Gordon

```html
<!DOCTYPE html>
<html lang="en">
<head>
<meta charset="utf-8">
<title>Toriva Letterhead</title>
<link href="https://fonts.googleapis.com/css2?family=Cinzel:wght@500&family=Open+Sans:wght@400&family=Montserrat:wght@500&display=swap" rel="stylesheet">
<style>
  :root {
    --navy: #1d3a78;
    --ink: #3a3f4a;
    --paper: #ffffff;
    --edge: #d6d8dc;
  }
  html, body {
    margin: 0;
    padding: 0;
    overflow: hidden;
    background: var(--paper);
  }
  .letterhead {
    position: relative;
    width: 849px;
    height: 1200px;
    box-sizing: border-box;
    border: 1px solid var(--edge);
    background: var(--paper);
    overflow: hidden;
  }
  .brand {
    position: absolute;
    left: 52px;
    top: 58px;
    display: flex;
    align-items: center;
    gap: 18px;
  }
  .brand-square {
    width: 58px;
    height: 58px;
    background: var(--navy);
  }
  .brand-name {
    font-family: "Cinzel", serif;
    font-weight: 500;
    font-size: 40px;
    letter-spacing: 0.5px;
    color: var(--navy);
    line-height: 1;
  }
  .contact {
    position: absolute;
    left: 578px;
    top: 52px;
    margin: 0;
    padding: 0;
    list-style: none;
    font-family: "Open Sans", sans-serif;
    font-size: 17px;
    color: var(--ink);
  }
  .contact li {
    display: flex;
    align-items: center;
    gap: 10px;
    height: 27px;
  }
  .contact svg {
    width: 18px;
    height: 18px;
    fill: var(--navy);
    flex: none;
  }
  .contact .email {
    font-size: 15px;
  }
  .address-band {
    position: absolute;
    left: 48px;
    right: 48px;
    bottom: 8px;
    height: 36px;
    background: var(--navy);
    color: #ffffff;
    font-family: "Montserrat", sans-serif;
    font-weight: 500;
    font-size: 15px;
    letter-spacing: 5px;
    text-transform: uppercase;
    display: flex;
    align-items: center;
    padding-left: 14px;
    white-space: nowrap;
  }
</style>
</head>
<body>
  <div class="letterhead">
    <header class="brand">
      <div class="brand-square"></div>
      <div class="brand-name">ToriVaCapital</div>
    </header>

    <ul class="contact">
      <li>
        <svg viewBox="0 0 24 24" aria-hidden="true"><path d="M3 9c0-3 4-5 9-5s9 2 9 5v2h-5V9H8v2H3z M6 12h12l2 8H4z M12 14a2.5 2.5 0 1 0 0 5a2.5 2.5 0 1 0 0-5z"/></svg>
        <span>469.517.3846</span>
      </li>
      <li>
        <svg viewBox="0 0 24 24" aria-hidden="true"><path d="M7 2h10a1 1 0 0 1 1 1v18a1 1 0 0 1-1 1H7a1 1 0 0 1-1-1V3a1 1 0 0 1 1-1zm1 3v13h8V5z M11 19.2h2v1.4h-2z"/></svg>
        <span>214.639.4705</span>
      </li>
      <li class="email">
        <svg viewBox="0 0 24 24" aria-hidden="true"><path d="M2 5h20v14H2z M3.5 6.5v.6L12 13l8.5-5.9v-.6z" fill-rule="evenodd"/></svg>
        <span>gwhitfield@torivafunds.example</span>
      </li>
    </ul>

    <footer class="address-band">4120 Marlow Crest Drive, Suite 210,&nbsp; Plano Texas 75081</footer>
  </div>
</body>
</html>
```